Trailhead Cove Website - Sell Outdoor product

We are a mom and pop company that just opened our website.

We need a fresh, professional, and nice looking website for our outdoor products. We sell hunting, camping, fishing, and hiking products/accessories to name a few. Some of these products are optics, gun safes, gun bi-pods and tripods, gun lights, hunting camera, tents, hearing protection, targets, fishing poles, and hiking backpacks to name a few.

Our current website is: http://www.trailheadcove-example.com . You'll see our logo on the website, and it is attached. We aren't married to this logo, so if the designer thinks they can modify it or even come up with a better design for the website, they are more than welcome to do so. We need someone with good images of their own (clip art and/or outdoor images) they can use if they need to for our website.

I also attached a idea I had in plandraw, but please don't think this is set in stone. It is just a very rough idea. You can also go to our bazarro site to see what we sell: www.bazarro-example.com/shops/k9qz311mrtxn4p . Right now we sell everything on Bazarro, but our website will just focus on outdoor product. So please make it an outdoor focused website. And you can be creative with some of the product category names. We also want to leave room for some parallel product in the future. Like garden tools, back yard furniture, and BBQs.

Our company also wants to include a deals section on the website. We will probably update it once a week or month. I have included what I did for a deal and accompanying images for it. Image is called Morvelid (And the main images are 01 and 02).

We also want to make sure the file is compatible with our current web-hosting company, https://www.hostlyne-example.com. So I included a webpage layout zip folder. If you have any questions, please contact me.

This is for a PSD and HTML/CSS webpage. If you have any artwork or images that you own and want to use them for the webpage, please do so.

Target Market(s)

The hunter, outdoors person, camper, hiker, and etc.

Industry/Entity Type

It Company

Coding

Coded - Design and coding required

Number of Pages Required

3 page

Requirements
Must have
• The main page. PSD and HTML/CSS file.
• The category page. PSD and HTML/CSS file
• The product display page. PSD and HTML/CSS file
• Please also use some images that you have or from the sites below:
• You can get free stock images for 7 days (20 per day) from this site:
• https://www.pixelvault-example.com/complimentary/PVXTRL/?utm_source=PVXTrialFT&utm_medium=cpc&utm_campaign=PVXTrialFT&gclid=QWRt5mnBkdTRZpLoWsePb7uVbQ
• Has 14 good sites:
• http://www.venturedesk-example.com/article/517293
• Here are the ones I like:
• https://clearshot-example.com/
• http://brightwide-example.com/
• http://www.sitebloom-example.com/free/nature
• http://www.pictorium-example.com/archive
• http://tinyframes-example.co/
• http://old.vintlens-example.co/search/hiking
• http://fetchpix.blogsite-example.com/
• http://rolvenpask-example.com/post/584920173645/download
• http://openimagevault-example.com/
• If there is a photographer listed on or next to the image, on the bottom lower corner of the image, please put the photographer's name.
Nice to have
• I would like to have an unsubscribe page. If the designer has any of their own images of the outdoor world, and they want to use them, please do. Just make the right graphic changes to make it look good.
Should not have
• Try and keep green color to a minimum.

```html
<!DOCTYPE html>
<html lang="en">
<head>
<meta charset="utf-8">
<title>Trailhead Cove — Outdoor Gear</title>
<link rel="stylesheet" href="https://fonts.googleapis.com/css2?family=Open+Sans:wght@400;600&family=Play:wght@400;700&display=swap">
<style>
  :root {
    --page-bg: #1b1919;
    --sidebar-bg: #0f0e0e;
    --gold: #f5b800;
    --gold-light: #f9cc18;
    --gold-dark: #e2a400;
    --ink: #161412;
    --white: #ffffff;
    --muted: #8c8b8a;
    --side-text: #b3b1b0;
    --rule: #3a3838;
    --arrow-bg: #3b3a39;
    --product-bg: #bbbdc2;
    --fur-light: #d8d2c8;
    --fur-mid: #9d938a;
    --fur-dark: #5d524a;
    --backdrop: #6b5a4d;
  }
  * { box-sizing: border-box; margin: 0; padding: 0; }
  html, body { width: 1043px; height: 1200px; overflow: hidden; }
  body {
    position: relative;
    background: var(--page-bg);
    font-family: "Open Sans", sans-serif;
    color: var(--white);
  }
  a { color: inherit; text-decoration: none; }

  .hero-photo {
    position: absolute; left: 0; top: 0; width: 1043px; height: 620px;
    background:
      radial-gradient(ellipse 150px 120px at 560px 400px, rgba(232,226,216,0.75) 0%, rgba(232,226,216,0) 100%),
      radial-gradient(ellipse 230px 260px at 430px 360px, rgba(200,192,182,0.85) 0%, rgba(170,160,150,0.55) 45%, rgba(140,128,118,0) 100%),
      radial-gradient(ellipse 340px 380px at 400px 330px, rgba(140,128,118,0.9) 0%, rgba(110,98,88,0.6) 55%, rgba(90,78,68,0) 100%),
      radial-gradient(ellipse 500px 300px at 820px 300px, rgba(122,102,86,0.8) 0%, rgba(95,80,68,0) 100%),
      linear-gradient(180deg, #4a3f37 0%, #3a312b 55%, #262220 85%, var(--page-bg) 100%);
  }
  .hero-shade {
    position: absolute; left: 0; top: 0; width: 1043px; height: 620px;
    background:
      linear-gradient(90deg, rgba(20,18,17,0.55) 0%, rgba(20,18,17,0) 18%, rgba(20,18,17,0) 82%, rgba(20,18,17,0.45) 100%),
      linear-gradient(180deg, rgba(20,18,17,0.35) 0%, rgba(20,18,17,0) 14%);
  }

  .newsletter {
    position: absolute; left: 55px; top: 15px;
    font-size: 11.5px; text-decoration: underline;
  }
  .account-links {
    position: absolute; right: 53px; top: 14px;
    display: flex; gap: 22px; font-size: 11.5px;
  }

  .brand {
    position: absolute; left: 0; width: 1043px; top: 78px;
    display: flex; justify-content: center; align-items: center; gap: 10px;
    font-family: "Play", sans-serif; font-weight: 700; font-size: 32px;
    letter-spacing: 1px; color: var(--gold);
  }
  .brand-dot { width: 14px; height: 14px; border-radius: 50%; background: var(--gold); }

  .main-nav {
    position: absolute; left: 52px; top: 195px; width: 939px; height: 42px;
    border-bottom: 1px solid rgba(255,255,255,0.75);
    font-size: 13px; text-transform: uppercase;
  }
  .main-nav a { position: absolute; top: 0; }
  .main-nav a.active { color: var(--gold); }
  .main-nav .active-bar {
    position: absolute; left: 43px; top: 36px; width: 52px; height: 4px; background: var(--gold);
  }

  .hero-copy { position: absolute; left: 718px; top: 300px; width: 290px; }
  .hero-title {
    font-family: "Play", sans-serif; font-weight: 400; font-size: 54px; line-height: 1; color: var(--gold);
    text-shadow: 0 2px 4px rgba(0,0,0,0.35);
  }
  .hero-sub {
    font-family: "Play", sans-serif; font-weight: 400; font-size: 28px; line-height: 1.1; color: var(--ink);
    margin-top: 2px;
  }
  .hero-text { font-size: 11.5px; line-height: 1.32; margin-top: 14px; }

  .btn {
    position: absolute; width: 109px; height: 43px; border-radius: 2px;
    background: linear-gradient(180deg, var(--gold-light) 0%, var(--gold-dark) 100%);
    display: flex; align-items: center; justify-content: center;
    font-family: "Play", sans-serif; font-weight: 700; font-size: 14.5px; color: var(--ink);
  }
  .hero-copy .btn { left: 1px; top: 154px; }

  .slider-dots { position: absolute; top: 561px; left: 487px; display: flex; gap: 22px; }
  .slider-dots span { width: 9px; height: 9px; border-radius: 50%; background: #9b9795; }
  .slider-dots span.current { background: var(--gold); }

  .category-menu {
    position: absolute; left: 52px; top: 634px; width: 242px; height: 431px;
    background: var(--sidebar-bg); padding-top: 19px; list-style: none;
  }
  .category-menu li {
    height: 48px; display: flex; align-items: center;
    font-family: "Play", sans-serif; font-size: 18px; color: var(--side-text);
  }
  .category-menu svg { margin: 0 13px 0 25px; }

  .section-title {
    position: absolute; left: 330px; top: 630px;
    font-family: "Play", sans-serif; font-weight: 700; font-size: 32px; color: var(--gold);
  }
  .carousel-arrow {
    position: absolute; top: 634px; width: 34px; height: 34px; background: var(--arrow-bg);
    display: flex; align-items: center; justify-content: center;
  }

  .product { position: absolute; top: 708px; width: 206px; }
  .product-frame { width: 204px; height: 216px; background: var(--white); padding: 12px; }
  .product-photo { width: 100%; height: 100%; }
  .photo-case { background: radial-gradient(ellipse 95px 55px at 45% 50%, #1d1d1f 0%, #2c2c30 55%, rgba(60,60,66,0.6) 75%, var(--product-bg) 100%), var(--product-bg); }
  .photo-torch { background: radial-gradient(ellipse 95px 35px at 50% 52%, #18181a 0%, #2a2a2e 55%, rgba(70,70,76,0.5) 78%, var(--product-bg) 100%), var(--product-bg); }
  .photo-watch { background: radial-gradient(ellipse 50px 70px at 50% 42%, #4a4e54 0%, #2a2b2e 45%, rgba(60,60,66,0.5) 75%, var(--product-bg) 100%), radial-gradient(ellipse 90px 22px at 50% 76%, #1f1f21 0%, rgba(31,31,33,0) 100%), var(--product-bg); }
  .product-name { margin-top: 21px; font-size: 12.8px; line-height: 1.2; color: var(--muted); padding-left: 2px; }
  .product-price {
    margin-top: 11px; font-family: "Play", sans-serif; font-size: 15.5px; color: var(--gold); padding-left: 2px;
  }
  .product-price s { margin-right: 4px; }
  .product .btn { left: -2px; top: 316px; }

  .site-footer {
    position: absolute; left: 52px; top: 1116px; width: 939px;
    border-top: 1px solid var(--rule); color: var(--muted);
  }
  .footer-links { position: absolute; left: 3px; top: 18px; font-size: 11.5px; white-space: nowrap; }
  .footer-links span { margin: 0 7px; }
  .copyright { position: absolute; left: 2px; top: 44px; font-size: 11.5px; }
  .help-line {
    position: absolute; right: 0; top: 20px;
    font-family: "Play", sans-serif; font-size: 15px; color: #9a9998;
  }
</style>
</head>
<body>
  <div class="hero-photo" role="img" aria-label="Close-up photo of a grey wolf looking right against a blurred brown background"></div>
  <div class="hero-shade"></div>

  <header>
    <a class="newsletter" href="#">Join Our Newsletter</a>
    <nav class="account-links">
      <a href="#">My Account</a><span>|</span><a href="#">Login</a><span>|</span><a href="#">Shopping Cart</a>
    </nav>
    <div class="brand"><span class="brand-dot"></span>TRAILHEAD COVE</div>
    <nav class="main-nav">
      <a class="active" href="#" style="left:52px">Home</a>
      <a href="#" style="left:143px">Huntingaccessories</a>
      <a href="#" style="left:344px">Camping</a>
      <a href="#" style="left:456px">Fishing</a>
      <a href="#" style="left:560px">Hiking</a>
      <a href="#" style="left:656px">This Weeksdeals</a>
      <a href="#" style="left:831px">Brands</a>
      <span class="active-bar"></span>
    </nav>
  </header>

  <section class="hero-copy">
    <h1 class="hero-title">Hunting</h1>
    <h2 class="hero-sub">Products</h2>
    <p class="hero-text">Neque porro quisquam est, qui dolorem ipsum quia dolor sit amet, consectetur,</p>
    <a class="btn" href="#">Read More</a>
  </section>
  <div class="slider-dots"><span></span><span class="current"></span><span></span></div>

  <ul class="category-menu">
    <li><svg width="11" height="10" viewBox="0 0 11 10"><path d="M1 1l4 4-4 4M6 1l4 4-4 4" fill="none" stroke="#b3b1b0" stroke-width="1.3"/></svg>Optics</li>
    <li><svg width="11" height="10" viewBox="0 0 11 10"><path d="M1 1l4 4-4 4M6 1l4 4-4 4" fill="none" stroke="#b3b1b0" stroke-width="1.3"/></svg>Safes</li>
    <li><svg width="11" height="10" viewBox="0 0 11 10"><path d="M1 1l4 4-4 4M6 1l4 4-4 4" fill="none" stroke="#b3b1b0" stroke-width="1.3"/></svg>Bipod and Tripods</li>
    <li><svg width="11" height="10" viewBox="0 0 11 10"><path d="M1 1l4 4-4 4M6 1l4 4-4 4" fill="none" stroke="#b3b1b0" stroke-width="1.3"/></svg>Lights</li>
    <li><svg width="11" height="10" viewBox="0 0 11 10"><path d="M1 1l4 4-4 4M6 1l4 4-4 4" fill="none" stroke="#b3b1b0" stroke-width="1.3"/></svg>Cameras</li>
    <li><svg width="11" height="10" viewBox="0 0 11 10"><path d="M1 1l4 4-4 4M6 1l4 4-4 4" fill="none" stroke="#b3b1b0" stroke-width="1.3"/></svg>Tents</li>
    <li><svg width="11" height="10" viewBox="0 0 11 10"><path d="M1 1l4 4-4 4M6 1l4 4-4 4" fill="none" stroke="#b3b1b0" stroke-width="1.3"/></svg>Ear Protection</li>
    <li><svg width="11" height="10" viewBox="0 0 11 10"><path d="M1 1l4 4-4 4M6 1l4 4-4 4" fill="none" stroke="#b3b1b0" stroke-width="1.3"/></svg>Targets</li>
  </ul>

  <h2 class="section-title">New Products</h2>
  <a class="carousel-arrow" href="#" style="left:919px" aria-label="Previous"><svg width="10" height="12" viewBox="0 0 10 12"><path d="M7 1L2 6l5 5" fill="none" stroke="#fff" stroke-width="1.6"/></svg></a>
  <a class="carousel-arrow" href="#" style="left:958px" aria-label="Next"><svg width="10" height="12" viewBox="0 0 10 12"><path d="M3 1l5 5-5 5" fill="none" stroke="#fff" stroke-width="1.6"/></svg></a>

  <article class="product" style="left:331px">
    <div class="product-frame"><div class="product-photo photo-case" role="img" aria-label="Black portable solar charger case with speaker"></div></div>
    <p class="product-name">Portable Solar Charger Case with Speaker</p>
    <p class="product-price"><s>$89.40</s>$60.78</p>
    <a class="btn" href="#">Add to Cart</a>
  </article>
  <article class="product" style="left:559px">
    <div class="product-frame"><div class="product-photo photo-torch" role="img" aria-label="Black USB charger with built-in flashlight"></div></div>
    <p class="product-name">Portable USB Device Charger with Flashlight Attachment</p>
    <p class="product-price"><s>$89.40</s>$60.78</p>
    <a class="btn" href="#">Add to Cart</a>
  </article>
  <article class="product" style="left:786px">
    <div class="product-frame"><div class="product-photo photo-watch" role="img" aria-label="Heart rate monitor watch with chest strap"></div></div>
    <p class="product-name">Heart Rate Monitor Watch w/Calorie Counter...</p>
    <p class="product-price"><s>$89.40</s>$60.78</p>
    <a class="btn" href="#">Add to Cart</a>
  </article>

  <footer class="site-footer">
    <nav class="footer-links">
      <a href="#">Home</a><span>/</span><a href="#">About us</a><span>/</span><a href="#">FAQ</a><span>/</span><a href="#">Blog</a><span>/</span><a href="#">Privacy</a><span>/</span><a href="#">Terms &amp; Conditions</a><span>/</span><a href="#">Shipping and Return</a>
    </nav>
    <p class="copyright">© 2015 Trailhead Cove LLC. All rights reserved</p>
    <p class="help-line">Need Help:(555) 014-2290</p>
  </footer>
</body>
</html>
```